New Interrior Decoration company needs new website

We need a website for our new company specialising in interior decoration to residential and commercial markets.
We supply and install decorative and printed films for office and home decoration such as feature walls.
We would like to keep the design simple and clean.

Target Market(s)

Architects and interior designaers

Industry/Entity Type

It Company

Number of Pages Required

5+ page

Font styles to use
Sans Serif

Requirements
Must have
• Home page,
• Services/products page (split into commercial and residential)
• Gallery (split into commercial and residential)
• contact form and page
Nice to have
• Very clean and minimalistic design.

```html
<!DOCTYPE html>
<html lang="en">
<head>
<meta charset="utf-8">
<title>Arden Interiors</title>
<link rel="stylesheet" href="https://fonts.googleapis.com/css2?family=Open+Sans:wght@400;600;700&family=Raleway:wght@400;500;700&display=swap">
<style>
  :root {
    --blue: #0a5cb8;
    --ink: #222;
    --body: #555;
    --dark: #3a3a3a;
    --bar: #333;
    --light: #e8e8e8;
    --white: #fff;
  }
  * { box-sizing: border-box; margin: 0; padding: 0; }
  html, body { width: 1200px; height: 2961px; overflow: hidden; }
  body { position: relative; background: var(--white); font-family: "Open Sans", Arial, sans-serif; color: var(--body); }
  .abs { position: absolute; }
  .heading { font-family: "Raleway", Arial, sans-serif; font-weight: 400; font-size: 43px; color: var(--ink); text-align: center; left: 0; width: 1200px; letter-spacing: 0.5px; white-space: nowrap; }
  .heading .accent { color: var(--blue); }
  .btn { position: absolute; display: flex; align-items: center; justify-content: center; background: var(--blue); color: var(--white); font-family: "Open Sans", Arial, sans-serif; font-size: 19px; text-transform: uppercase; border-radius: 2px; white-space: nowrap; }

  /* header */
  .site-header { left: 0; top: 0; width: 1200px; height: 105px; background: var(--white); }
  .brand { left: 77px; top: 20px; height: 66px; display: flex; align-items: center; gap: 14px; }
  .brand-mark { width: 62px; height: 62px; background: var(--blue); flex: none; }
  .brand-name { font-family: "Raleway", Arial, sans-serif; font-weight: 700; font-size: 31px; line-height: 31px; color: #1a1a1a; letter-spacing: 1px; }
  .main-nav a { position: absolute; top: 26px; height: 53px; display: flex; align-items: center; font-size: 20px; color: #333; text-decoration: none; white-space: nowrap; }
  .main-nav a.active { background: var(--blue); color: var(--white); padding: 0 20px; }

  /* hero */
  .hero { left: 0; top: 105px; width: 1200px; height: 574px; background: linear-gradient(180deg, #6f786d 0%, #5f685e 70%, #b9bcb6 82%, #d4d6d1 100%); }
  .hero-title { right: 55px; top: 126px; text-align: right; font-family: "Raleway", Arial, sans-serif; font-weight: 700; font-size: 38px; line-height: 61px; color: var(--white); white-space: nowrap; }
  .hero-cta { left: 938px; top: 286px; width: 197px; height: 57px; background: var(--white); color: var(--blue); font-weight: 700; font-size: 21px; }

  /* welcome */
  .welcome-title { top: 750px; }
  .welcome-text { left: 170px; top: 818px; width: 860px; text-align: center; font-size: 15px; line-height: 25px; color: #666; }
  .welcome-btn { left: 517px; top: 914px; width: 162px; height: 49px; }

  /* services */
  .services { left: 0; top: 1028px; width: 1200px; height: 344px; background: linear-gradient(135deg, #4a4a4a, #3d3d3d 60%, #555); }
  .services .heading { top: 56px; color: var(--white); }
  .service-photo { border: 2px solid #ddd; width: 209px; height: 140px; }
  .service-name { font-family: "Raleway", Arial, sans-serif; font-size: 26px; color: var(--white); white-space: nowrap; }
  .service-text { font-size: 15px; line-height: 25px; color: #eee; width: 262px; }
  .service-more { font-size: 17px; color: var(--white); white-space: nowrap; }

  /* gallery */
  .gallery-title { top: 1436px; }
  .tab { height: 52px; width: 187px; font-family: "Raleway", Arial, sans-serif; font-size: 25px; color: var(--white); display: flex; align-items: center; justify-content: center; position: absolute; top: 1494px; }
  .tab.residential { left: 403px; background: var(--blue); }
  .tab.commercial { left: 610px; background: var(--dark); }
  .gallery-item { width: 235px; height: 156px; position: absolute; }
  .view-all { left: 525px; top: 1942px; width: 150px; height: 52px; }

  /* contact */
  .contact { left: 0; top: 2059px; width: 1200px; height: 460px; background: var(--light); }
  .contact .heading { top: 52px; }
  .field { position: absolute; background: var(--white); border: 1px solid #d6d6d6; font-size: 15px; color: #777; padding: 10px 9px; }
  .submit { left: 529px; top: 345px; width: 142px; height: 52px; font-size: 22px; }

  /* footer */
  .site-footer { left: 0; top: 2519px; width: 1200px; height: 389px; background: linear-gradient(90deg, #2a73c8, #3a86d8 50%, #2d78cb); }
  .footer-nav a { position: absolute; top: 64px; font-size: 19px; color: var(--white); text-decoration: none; white-space: nowrap; }
  .rule { position: absolute; left: 330px; width: 540px; height: 1px; background: rgba(255,255,255,0.7); }
  .call { left: 330px; top: 146px; display: flex; align-items: center; color: var(--white); white-space: nowrap; }
  .call-label { font-family: "Raleway", Arial, sans-serif; font-size: 29px; }
  .call-icon { width: 60px; height: 60px; border: 2px solid var(--white); border-radius: 50%; display: flex; align-items: center; justify-content: center; margin: 0 20px; }
  .call-number { font-size: 33px; font-weight: 600; }
  .social { position: absolute; top: 262px; width: 56px; height: 56px; border-radius: 50%; border: 2px solid var(--white); }
  .social.first { background: #3a3a3a; border-color: #3a3a3a; }
  .copyright { left: 0; top: 2908px; width: 1200px; height: 53px; background: var(--bar); color: var(--white); font-size: 14px; display: flex; align-items: center; justify-content: center; }
  .copyright strong { font-weight: 700; margin-right: 4px; }
</style>
</head>
<body>

<header class="abs site-header">
  <div class="abs brand">
    <span class="brand-mark"></span>
    <span class="brand-name">ARDEN<br>INTERIORS</span>
  </div>
  <nav class="main-nav">
    <a class="active" style="left:490px">HOME</a>
    <a style="left:616px">ABOUT</a>
    <a style="left:732px">SERVICES</a>
    <a style="left:882px">GALLERY</a>
    <a style="left:1024px">CONTACT</a>
  </nav>
</header>

<section class="abs hero" role="img" aria-label="Interior scene: wooden sideboard with framed art and a pendant lamp against a grey-green textured wall">
  <h1 class="abs hero-title">LOREM IPSUM IS DUMMY<br>TEXT OF&nbsp; THE PRINTING.</h1>
  <div class="btn hero-cta">CONTACT US</div>
</section>

<section class="welcome">
  <h2 class="abs heading welcome-title">WELCOME TO <span class="accent">ARDEN INTERIORS</span></h2>
  <p class="abs welcome-text">Lorem Ipsum is simply dummy text of the printing and typesetting industry. Lorem Ipsum has been the industry's standard dummy text ever since the 1500s, when an unknown printer took a galley of type and scrambled it to make a type specimen book.</p>
  <div class="btn welcome-btn">READ MORE</div>
</section>

<section class="abs services">
  <h2 class="abs heading">SERVICES WE PROVIDE</h2>

  <div class="abs service-photo" style="left:77px;top:137px;background:linear-gradient(135deg,#cfd3d2,#8d9492 60%,#5d6462)" role="img" aria-label="Residential interior with bright windows and pendant lamps"></div>
  <div class="abs service-name" style="left:302px;top:130px">Residential Interiors</div>
  <p class="abs service-text" style="left:302px;top:166px">Lorem Ipsum is simply dummy text of the printing and typesetting industry Lorem Ipsum...</p>
  <div class="abs service-more" style="left:302px;top:255px">READ MORE »</div>

  <div class="abs service-photo" style="left:630px;top:137px;background:linear-gradient(135deg,#e9e6e0,#cbb9ad 55%,#9c8f86)" role="img" aria-label="Commercial corridor with a decorative printed feature wall"></div>
  <div class="abs service-name" style="left:854px;top:130px">Commercial Interiors</div>
  <p class="abs service-text" style="left:854px;top:166px">Lorem Ipsum is simply dummy text of the printing and typesetting industry Lorem Ipsum...</p>
  <div class="abs service-more" style="left:854px;top:255px">READ MORE »</div>
</section>

<section class="gallery">
  <h2 class="abs heading gallery-title">LATEST <span class="accent">GALLERY</span></h2>
  <div class="tab residential">Residential</div>
  <div class="tab commercial">Commercial</div>

  <div class="gallery-item" style="left:77px;top:1571px;background:linear-gradient(135deg,#b9a46a,#8f9a63 50%,#c8402f)" role="img" aria-label="Living room with striped wood feature wall and red chairs"></div>
  <div class="gallery-item" style="left:347px;top:1571px;background:linear-gradient(135deg,#4a2a22,#6b3a2a 50%,#c9b8c4)" role="img" aria-label="Dark lounge with white designer chair and lamp"></div>
  <div class="gallery-item" style="left:618px;top:1571px;background:linear-gradient(135deg,#d7d3cf,#c35a5a 45%,#4a74b0)" role="img" aria-label="Office room with colourful printed wall mural"></div>
  <div class="gallery-item" style="left:888px;top:1571px;background:linear-gradient(135deg,#d3d6d4,#6f7775 60%,#4e5452)" role="img" aria-label="Bright room with pendant lamps and grey wall"></div>

  <div class="gallery-item" style="left:77px;top:1749px;background:linear-gradient(135deg,#9a9896,#d9d6d2 50%,#6f6b66)" role="img" aria-label="Kitchen and dining area with globe pendant lights"></div>
  <div class="gallery-item" style="left:347px;top:1749px;background:linear-gradient(135deg,#8c8a60,#b7b38c 55%,#6c6a44)" role="img" aria-label="Olive-toned wall with framed print and low cabinet"></div>
  <div class="gallery-item" style="left:618px;top:1749px;background:linear-gradient(180deg,#6c3f45,#8e5a5e 60%,#e8e2dc)" role="img" aria-label="Lounge with white sofa against a plum wall"></div>
  <div class="gallery-item" style="left:888px;top:1749px;background:linear-gradient(135deg,#b9a46a,#8f9a63 50%,#c8402f)" role="img" aria-label="Living room with striped wood feature wall and red chairs"></div>

  <div class="btn view-all">VIEW ALL</div>
</section>

<section class="abs contact">
  <h2 class="abs heading">GET IN <span class="accent">TOUCH WITH US</span></h2>
  <div class="field" style="left:231px;top:140px;width:332px;height:46px">Enter Name</div>
  <div class="field" style="left:231px;top:207px;width:332px;height:46px">Enter Email</div>
  <div class="field" style="left:231px;top:274px;width:332px;height:46px">Enter Contact No.</div>
  <div class="field" style="left:584px;top:140px;width:385px;height:182px">Enter Message</div>
  <div class="btn submit">SUBMIT</div>
</section>

<footer class="abs site-footer" role="img" aria-label="Blue-tinted office scene with colleagues at work">
  <nav class="footer-nav">
    <a style="left:323px">HOME</a>
    <a style="left:434px">ABOUT</a>
    <a style="left:553px">SERVICES</a>
    <a style="left:676px">GALLERY</a>
    <a style="left:800px">CONTACT</a>
  </nav>
  <div class="rule" style="top:124px"></div>
  <div class="abs call">
    <span class="call-label">CALL US TODAY</span>
    <span class="call-icon">
      <svg width="28" height="28" viewBox="0 0 24 24" aria-hidden="true"><path fill="#fff" d="M6.6 10.8c1.4 2.8 3.8 5.1 6.6 6.6l2.2-2.2c.3-.3.7-.4 1-.2 1.1.4 2.3.6 3.6.6.6 0 1 .4 1 1V20c0 .6-.4 1-1 1C10.6 21 3 13.4 3 4c0-.6.4-1 1-1h3.5c.6 0 1 .4 1 1 0 1.3.2 2.5.6 3.6.1.3 0 .7-.2 1l-2.3 2.2z"/></svg>
    </span>
    <span class="call-number">555 014 2086</span>
  </div>
  <div class="rule" style="top:227px"></div>
  <span class="social first" style="left:454px"></span>
  <span class="social" style="left:533px"></span>
  <span class="social" style="left:612px"></span>
  <span class="social" style="left:691px"></span>
</footer>

<div class="abs copyright"><strong>© ARDEN INTERIORS</strong> - 2016. All Rights Reserved.</div>

</body>
</html>
```